ZESTORAMA Business Card Design

ZESTORAMA
Zestorama is a food van, serving high vibe delicious food to go. This business is dedicated to healthy delicious feel good food, beauty in service and a sustainable planet.

The van will operate in the south west of western Australia at music festivals events markets wherever people need great food to go!

I like the idea of vibrant green mixed with a yellow?? background with some rays like the sun through the background.
The font needs to say vibrant energetic
TO ME -vibrant energetic font has to appear to be on the move - perhaps with shading??

I like fusha if that works for font? but the colour has to say food too.

I would like a symbol on the card a simple V turned into a womans raised arms. This should be vibrant too.
Thank you
Blessings
Marisol

Target Market(s)

target lovers of healthy high vibe food. music festival goers. age 18- 50 feel. audiance conscious eaters of feel great food

Industry/Entity Type

Events

Contact Information for Business Card

ZESTORAMA
High Vibe Food
Van
Marisol -owner/opperator
0471583906
Face book symbol - ZESTORAMA

on the I would like a logo of a simple V turned into a womans arms up toward the sky flip side

My number and name again
Zestorama- feel great mobile food
Festivals, events, markets & where high vibe food 2 go is appreciated

Requirements
Nice to have
• Moving energetic font
colour that says high vibe and healthy food

a logo that is a simple V turned into a woman's raised arms in gratitude

```html
<!DOCTYPE html>
<html lang="en">
<head>
<meta charset="utf-8">
<title>Zestorama – Business Card</title>
<link href="https://fonts.googleapis.com/css2?family=Righteous&family=Questrial&display=swap" rel="stylesheet">
<style>
  :root {
    --fuchsia: #e8217a;
    --fuchsia-deep: #c0105f;
    --lime: #9fd62a;
    --leaf: #4fb534;
    --sun: #e6ee3a;
    --ink: #1a1a1a;
    --backdrop: #ecebe6;
  }
  * { box-sizing: border-box; margin: 0; padding: 0; }
  html, body { width: 1200px; height: 723px; overflow: hidden; }
  body {
    background: var(--backdrop);
    font-family: "Questrial", "Century Gothic", sans-serif;
    position: relative;
  }
  .card {
    position: absolute;
    top: 52px;
    width: 380px;
    height: 620px;
    border-radius: 6px;
    overflow: hidden;
    box-shadow: 0 6px 18px rgba(0,0,0,.18);
  }
  .card--back { left: 190px; }
  .card--front { left: 630px; }
  .rays {
    position: absolute; inset: 0;
    background:
      radial-gradient(circle at 50% 45%, var(--sun) 0%, var(--lime) 45%, var(--leaf) 100%);
  }
  .card__content {
    position: relative;
    height: 100%;
    padding: 26px 26px;
    display: flex;
    flex-direction: column;
    align-items: center;
    text-align: center;
  }
  .brand-mark {
    width: 120px; height: 120px;
    border-radius: 50%;
    background: var(--fuchsia);
    flex: none;
  }
  .wordmark {
    font-family: "Righteous", "Arial Black", sans-serif;
    color: var(--fuchsia);
    font-size: 46px;
    letter-spacing: 1px;
    line-height: 1;
  }
  /* back */
  .card--back .wordmark { font-size: 44px; margin-bottom: 8px; }
  .tagline {
    color: var(--fuchsia);
    font-weight: 700;
    font-size: 19px;
    line-height: 1.15;
    margin-bottom: 16px;
  }
  .card--back .brand-mark { width: 110px; height: 110px; margin-bottom: 18px; }
  .about {
    color: var(--fuchsia);
    font-size: 19px;
    line-height: 1.25;
    font-weight: 700;
  }
  .about__cta {
    display: block;
    margin-top: 6px;
    color: var(--ink);
    font-family: "Righteous", "Arial Black", sans-serif;
    font-size: 20px;
  }
  /* front */
  .card--front .brand-mark { margin: 10px 0 18px; }
  .subline {
    font-family: "Righteous", "Arial Black", sans-serif;
    color: var(--fuchsia);
    font-size: 25px;
    margin-top: 6px;
  }
  .contact-name, .contact-phone {
    color: var(--fuchsia);
    font-weight: 700;
    letter-spacing: 1px;
  }
  .contact-name { font-size: 28px; margin-top: 44px; }
  .contact-phone { font-size: 32px; margin-top: 28px; }
  .social {
    margin-top: auto;
    display: flex;
    align-items: center;
    gap: 10px;
    color: var(--fuchsia-deep);
    font-size: 20px;
    font-weight: 700;
  }
  .social__square {
    width: 28px; height: 28px;
    background: var(--fuchsia);
    border-radius: 4px;
  }
  .contact-email {
    margin-top: 12px;
    color: var(--ink);
    font-size: 21px;
    font-weight: 700;
    margin-bottom: 8px;
  }
</style>
</head>
<body>

  <article class="card card--back">
    <div class="rays" role="img" aria-label="Sunburst of green and yellow rays radiating from the centre"></div>
    <div class="card__content">
      <h2 class="wordmark">ZESTORAMA</h2>
      <p class="tagline">Feel Great Food<br>@ festivals,<br>community events &amp;<br>private gatherings</p>
      <div class="brand-mark" aria-hidden="true"></div>
      <p class="about">
        Dedicated to conscious, joyous eating.
        VIBRANT breakfasts, coconuts &amp; DELICIOUS
        nourishing soups. ZESTORAMA includes
        vegetarians, vegans &amp; gluten free folk!
        <span class="about__cta">Got The Vibe?</span>
      </p>
    </div>
  </article>

  <article class="card card--front">
    <div class="rays" role="img" aria-label="Sunburst of green and yellow rays radiating from the centre"></div>
    <div class="card__content">
      <div class="brand-mark" aria-hidden="true"></div>
      <h1 class="wordmark">ZESTORAMA</h1>
      <p class="subline">High Vibe Food Van</p>
      <p class="contact-name">Marisol</p>
      <p class="contact-phone">0471583906</p>
      <p class="social"><span class="social__square" aria-hidden="true"></span>Zestorama</p>
      <p class="contact-email">hello@zestoramavan.net</p>
    </div>
  </article>

</body>
</html>
```